A website for a Maltese Law Firm

Our law firm needs a website to further its business. The site should have a simple yet effective design. We would need the following sections: About us, Practice Areas, About Malta, Contact. These should be further split as follows:

About us: Our firm, Our values, What others say, Offices

Practice Areas: Crimimal, Citizenship & Residence, Sovereign Patron Pathway, Criminal Defence, Civil Litigation, Arbitration and ADR, Commercial and Corporate, Media Law.

About Malta: just one section.

Contact: Just one section

We would also need a news feed at the front of the site to include latest news regarding our cases.

At the bottom we need a section for our Terms and a Privacy Statement.

Our logo is being attached.

Target Market(s)

All clients looking for legal assistance in Malta

Industry/Entity Type

Legal

Coding

Coded - Design and coding required

Number of Pages Required

1 page

Requirements
Must have
• It must be simple yet striking.

```html
<!DOCTYPE html>
<html lang="en">
<head>
<meta charset="utf-8">
<title>Aquilina Zerafa Advocates</title>
<link rel="stylesheet" href="https://fonts.googleapis.com/css2?family=Cinzel:wght@400;600&family=Raleway:wght@400;600;700&display=swap">
<style>
:root{
  --ink:#2d2d2d;
  --text:#555;
  --muted:#777;
  --line:#cfcfcf;
  --dark:#333333;
  --grey-band:#efefef;
  --white:#ffffff;
}
*{box-sizing:border-box;margin:0;padding:0}
html,body{width:1200px;height:2397px;overflow:hidden}
body{font-family:"Raleway",sans-serif;color:var(--text);background:var(--white);position:relative}
a{color:inherit;text-decoration:none}

/* top bar */
.topbar{position:absolute;top:0;left:0;width:1200px;height:35px;border-bottom:1px solid #e2e2e2}
.social-cells{position:absolute;left:99px;top:0;display:flex}
.social-cells span{width:39px;height:35px;border-left:1px solid #e2e2e2;display:flex;align-items:center;justify-content:center}
.social-cells span:last-child{border-right:1px solid #e2e2e2}
.social-cells i{width:10px;height:10px;border-radius:50%;background:#666}
.callbar{position:absolute;left:880px;top:0;width:221px;height:35px;background:var(--dark);color:#fff;font-size:12px;letter-spacing:1px;display:flex;align-items:center;justify-content:center;gap:10px}

/* header */
.header{position:absolute;top:35px;left:0;width:1200px;height:77px}
.wordmark{position:absolute;left:99px;top:22px;display:flex;align-items:center;gap:10px;font-family:"Raleway",sans-serif;font-weight:600;font-size:22px;color:var(--ink);line-height:1}
.wordmark i{width:14px;height:14px;background:var(--ink)}
.nav{position:absolute;right:99px;top:30px;display:flex;gap:36px;font-family:"Cinzel",serif;font-size:14px;color:var(--ink)}
.nav a{padding-top:5px}
.nav a.active{border-bottom:2px solid var(--ink);border-top:1px solid var(--ink);padding:4px 4px 6px}

/* hero */
.hero{position:absolute;top:112px;left:0;width:1200px;height:465px;background:linear-gradient(100deg,#3a3a3a 0%,#8a8580 35%,#c9c2b8 55%,#5a2a22 72%,#3b2b25 100%)}
.hero-title{position:absolute;left:99px;top:190px;font-family:"Cinzel",serif;font-weight:400;color:#fff;font-size:26px;line-height:34px;letter-spacing:1px}
.hero-btn{position:absolute;left:99px;top:276px;border:1px solid #fff;color:#fff;font-family:"Cinzel",serif;font-size:12.5px;padding:8px 10px}
.hero-arrow{position:absolute;top:196px}

/* section headings */
.section-title{position:absolute;left:0;width:1200px;text-align:center;font-family:"Cinzel",serif;font-weight:400;font-size:25px;color:#777;letter-spacing:1px}
.section-title b{font-weight:400;color:var(--ink);border-top:1px solid var(--ink);border-bottom:2px solid var(--ink);padding:0 2px}

/* about */
.about-title{position:absolute;left:99px;top:640px;font-family:"Cinzel",serif;font-weight:400;font-size:25px;color:#777}
.about-title b{font-weight:400;color:var(--ink);border-top:1px solid var(--ink);border-bottom:2px solid var(--ink);padding:0 4px;margin-left:8px}
.about-text{position:absolute;left:99px;top:688px;width:595px;font-size:12.5px;line-height:25.5px;color:var(--text)}
.btn-dark{position:absolute;background:var(--dark);color:#fff;font-family:"Cinzel",serif;font-size:13px;display:flex;align-items:center;justify-content:center}
.value{position:absolute;left:748px;width:355px}
.value .icon{position:absolute;left:0;top:0;width:96px;height:96px;border:1px solid var(--line);display:flex;align-items:center;justify-content:center}
.value h3{position:absolute;left:115px;top:4px;font-family:"Cinzel",serif;font-weight:400;font-size:17px;color:var(--ink)}
.value p{position:absolute;left:115px;top:30px;width:240px;font-size:12px;line-height:19.5px;color:var(--muted)}

/* practice */
.practice{position:absolute;top:946px;left:0;width:1200px;height:350px;background:var(--grey-band)}
.card{position:absolute;top:1063px;width:152px;text-align:center}
.card .box{height:97px;border:1px solid var(--line);background:#f7f7f7;display:flex;align-items:center;justify-content:center}
.card .label{height:58px;display:flex;align-items:center;justify-content:center;font-family:"Cinzel",serif;font-weight:600;font-size:12.5px;line-height:15px;color:var(--ink);border-bottom:1px solid #bbb}
.dots{position:absolute;top:1242px;left:582px;display:flex;gap:5px}
.dots i{width:9px;height:9px;border:1px solid #888;border-radius:50%}
.dots i.on{background:#888;box-shadow:inset 0 0 0 2px var(--grey-band)}

/* malta */
.malta-frame{position:absolute;left:99px;top:1401px;width:422px;height:248px;border:1px solid #ddd;background:#fff}
.malta-img{position:absolute;left:115px;top:1419px;width:422px;height:248px;background:linear-gradient(180deg,#4d6f9c 0%,#7c9bc0 40%,#c88a4a 55%,#6a6fae 70%,#3e67a8 100%)}
.malta-text{position:absolute;left:566px;top:1406px;width:535px;font-size:12.5px;line-height:25.5px;color:var(--text)}
.bullets{position:absolute;left:566px;top:1564px;width:540px;list-style:none;font-size:12px;font-weight:700;color:var(--ink);line-height:17px}
.bullets li{position:relative;padding-left:24px;margin-bottom:14px}
.bullets svg{position:absolute;left:0;top:3px}

/* news */
.news{position:absolute;top:1721px;left:0;width:1200px;height:454px;background:linear-gradient(90deg,#f3f4f7 0%,#e8ebf0 60%,#dde2ea 100%)}
.post{position:absolute;top:1834px;width:479px}
.post .photo{position:relative;height:173px}
.post .date{position:absolute;left:0;bottom:0;width:61px;height:61px;background:rgba(30,30,30,.9);color:#fff;text-align:center;padding-top:8px}
.post .date b{display:block;font-size:21px;line-height:22px}
.post .date span{font-size:13px}
.post p{margin-top:20px;font-size:12.5px;line-height:25.5px;color:var(--text)}
.btn-line{position:absolute;top:254px;left:0;width:126px;height:36px;border:1px solid var(--dark);font-family:"Cinzel",serif;font-size:13px;color:var(--ink);display:flex;align-items:center;justify-content:center}

/* footer */
.footer{position:absolute;top:2175px;left:0;width:1200px;height:222px;background:var(--dark);color:#ddd}
.fwordmark{position:absolute;left:99px;top:88px;font-family:"Raleway",sans-serif;font-weight:600;font-size:20px;color:#fff;line-height:1}
.copyright{position:absolute;left:99px;top:136px;font-size:11.5px;color:#ddd}
.fhead{position:absolute;top:45px;font-family:"Cinzel",serif;font-weight:400;font-size:16px;color:#fff;letter-spacing:1px;border-bottom:1px solid #777;padding-bottom:6px}
.flinks a{position:absolute;font-size:11.5px;color:#ccc;padding-left:20px}
.flinks a::before{content:"";position:absolute;left:2px;top:3px;width:6px;height:6px;border:1px solid #bbb;transform:rotate(45deg)}
.fsocial{position:absolute;left:592px;top:170px;display:flex;gap:15px}
.fsocial i{width:10px;height:10px;border-radius:50%;background:#eee}
.newsletter{position:absolute;left:799px;top:93px;width:302px;height:33px;display:flex}
.newsletter .field{flex:1;background:#4a4a4a;font-size:11.5px;font-style:italic;color:#ccc;display:flex;align-items:center;padding-left:15px}
.newsletter .send{width:47px;background:#d8d8d8;display:flex;align-items:center;justify-content:center}
.contact-line{position:absolute;font-size:11.5px;color:#ddd;display:flex;align-items:center;gap:8px}
</style>
</head>
<body>

<div class="topbar">
  <div class="social-cells"><span><i></i></span><span><i></i></span><span><i></i></span><span><i></i></span></div>
  <div class="callbar">
    <svg width="16" height="16" viewBox="0 0 16 16"><circle cx="8" cy="8" r="7.5" fill="#555"/><path d="M5 4.5l1.6-.5 1 2-1 .8c.5 1 1.2 1.8 2.2 2.3l.8-1 2 1-.5 1.6c-3 0-6-3-6.1-6.2z" fill="#fff"/></svg>
    <span>CALL US : (356) 2000 4817</span>
  </div>
</div>

<header class="header">
  <div class="wordmark"><i></i><span>Aquilina Zerafa</span></div>
  <nav class="nav">
    <a class="active" href="#">Home</a><a href="#">About us</a><a href="#">Practice Areas</a><a href="#">About Malta</a><a href="#">Contact</a>
  </nav>
</header>

<section class="hero" role="img" aria-label="Photo of a wooden judge's gavel on a desk beside an open book">
  <svg class="hero-arrow" style="left:27px" width="44" height="44" viewBox="0 0 44 44" fill="none" stroke="#fff" stroke-width="2"><path d="M14 4h26v36H14"/><path d="M30 22H4M12 14l-8 8 8 8"/></svg>
  <svg class="hero-arrow" style="right:27px" width="44" height="44" viewBox="0 0 44 44" fill="none" stroke="#fff" stroke-width="2"><path d="M30 4H4v36h26"/><path d="M14 22h26M32 14l8 8-8 8"/></svg>
  <h1 class="hero-title">The Greatest &amp; Stongest<br>Firm You Can Trust</h1>
  <a class="hero-btn" href="#">Request A Free Consultant</a>
</section>

<section class="about">
  <h2 class="about-title">About<b>Aquilina Zerafa</b></h2>
  <p class="about-text">Lorem ipsum dolor sit amet, consectetuer adipiscing elit, sed diam nonummy nibh euismod tincidunt ut laoreet dolore magna aliquam erat volutpat. Ut wisi enim ad minim veniam, quis nostrud exerci tation ullamcorper suscipit lobortis nisl ut aliquip ex ea commodo consequat. Duis autem vel eum iriure dolor in hendrerit in vulputate velit esse molestie consequat, vel illum dolore eu feugiat nulla facilisis at vero eros et accumsan et iusto odio dignissim qui blandit praesent luptatum&nbsp; te feugait nulla facilisi.</p>
  <a class="btn-dark" href="#" style="left:99px;top:857px;width:134px;height:38px">Read More</a>

  <div class="value" style="top:663px">
    <div class="icon"><svg width="58" height="40" viewBox="0 0 58 40" fill="#2d2d2d"><path d="M2 10l10-6 6 3-12 20-4-3zM56 10l-10-6-6 3 12 20 4-3z"/><path d="M18 8l10 1-6 7c2 2 4 2 6 0l6-5 10 12-3 3-8 8-4 2-14-10-3-3z"/></svg></div>
    <h3>Our Values</h3>
    <p>Artis nisl ut aliquip ex ea commodoll eros et accumsan o digniss qui nulla facilisi...[+]</p>
  </div>
  <div class="value" style="top:792px">
    <div class="icon"><svg width="50" height="46" viewBox="0 0 50 46" fill="#2d2d2d"><path d="M25 2L3 12h44z"/><rect x="5" y="14" width="40" height="3"/><rect x="9" y="19" width="5" height="18"/><rect x="18" y="19" width="5" height="18"/><rect x="27" y="19" width="5" height="18"/><rect x="36" y="19" width="5" height="18"/><rect x="4" y="39" width="42" height="3"/><rect x="2" y="43" width="46" height="3"/></svg></div>
    <h3>Our firm</h3>
    <p>Artis nisl ut aliquip ex ea commodoll eros et accumsan o digniss qui nulla facilisi...[+]</p>
  </div>
</section>

<section class="practice"></section>
<h2 class="section-title" style="top:986px">Practice <b>Areas</b></h2>

<div class="card" style="left:99px">
  <div class="box"><svg width="62" height="52" viewBox="0 0 62 52" fill="none" stroke="#2d2d2d" stroke-width="4"><circle cx="16" cy="34" r="11"/><circle cx="44" cy="22" r="11"/><path d="M24 26l10-6M10 20l6-10 8 4M50 8l6 6"/></svg></div>
  <div class="label">Criminal Law</div>
</div>
<div class="card" style="left:310px">
  <div class="box"><svg width="52" height="44" viewBox="0 0 52 44" fill="#2d2d2d"><path d="M26 2L2 22h6v20h13V30h10v12h13V22h6L38 12V4h-6v3z"/></svg></div>
  <div class="label">Citizenship &amp;<br>Residence</div>
</div>
<div class="card" style="left:523px">
  <div class="box"><svg width="50" height="50" viewBox="0 0 50 50" fill="#2d2d2d"><circle cx="24" cy="15" r="11"/><path d="M4 48c0-12 8-20 20-20s20 8 20 20z"/><path d="M34 34l10 10 2-5 4-1z" fill="#fff" stroke="#2d2d2d" stroke-width="2"/></svg></div>
  <div class="label">Sovereign Patron<br>Pathway</div>
</div>
<div class="card" style="left:735px">
  <div class="box"><svg width="54" height="50" viewBox="0 0 54 50" fill="#2d2d2d"><rect x="18" y="4" width="14" height="24" rx="2" transform="rotate(45 25 16)"/><rect x="26" y="20" width="24" height="6" transform="rotate(45 26 20)"/><rect x="4" y="40" width="30" height="6"/></svg></div>
  <div class="label">Civil<br>Litigation</div>
</div>
<div class="card" style="left:949px">
  <div class="box"><svg width="50" height="48" viewBox="0 0 50 48" fill="#2d2d2d"><rect x="10" y="2" width="30" height="30" rx="2"/><circle cx="25" cy="13" r="6" fill="#f7f7f7"/><path d="M15 28c0-6 4-9 10-9s10 3 10 9z" fill="#f7f7f7"/><rect x="4" y="35" width="42" height="4"/><rect x="2" y="42" width="46" height="4"/></svg></div>
  <div class="label">Arbitration<br>and ADR</div>
</div>
<div class="dots"><i class="on"></i><i></i><i></i></div>

<section class="malta">
  <h2 class="section-title" style="top:1339px">About <b>Malta</b></h2>
  <div class="malta-frame"></div>
  <div class="malta-img" role="img" aria-label="Photo of Valletta's domed skyline lit at dusk across the harbour"></div>
  <p class="malta-text">Aeuismod tincidunt ut laoreet dolore magna aliquam erat volutpat. Ut wisi enim ad minim veniam, quis nostrud exerci tation ullamcorper suscipit lobortis nisl ut aliquip ex ea commodo consequat. Duis autem vel eum iriure dolor in hendrerit in vulputate velit esse molestie consequat, vel illum dolore eu feugiat nulla facilisis at vero eros et accumsan et iusto odio dignissim qui blandit praesent luptatum&nbsp; te feugait nulla facilisi.</p>
  <ul class="bullets">
    <li><svg width="13" height="12" viewBox="0 0 13 12" fill="none" stroke="#2d2d2d" stroke-width="1.4"><path d="M1 4h5V1l6 5-6 5V8H1z"/></svg>Duis autem vel eum iriure dolor in hendrerit in vulputate vl conseqt,molestie consequat vel illum dolore.</li>
    <li><svg width="13" height="12" viewBox="0 0 13 12" fill="none" stroke="#2d2d2d" stroke-width="1.4"><path d="M1 4h5V1l6 5-6 5V8H1z"/></svg>Ut wisi enim ad minim veniam, qui nostrud exeullamcorper suscipit lobortis .</li>
    <li><svg width="13" height="12" viewBox="0 0 13 12" fill="none" stroke="#2d2d2d" stroke-width="1.4"><path d="M1 4h5V1l6 5-6 5V8H1z"/></svg>Aulputate velit esse molestie consequat, vel illum dolore eu feugiat.</li>
  </ul>
</section>

<section class="news"></section>
<h2 class="section-title" style="top:1756px">Latest <b>News</b></h2>

<article class="post" style="left:99px">
  <div class="photo" role="img" aria-label="Photo of a lawyer reading case papers at a dark desk" style="background:linear-gradient(90deg,#1e1e1e 0%,#4a4f58 45%,#2a2a2a 100%)">
    <div class="date"><b>08</b><span>JUNE</span></div>
  </div>
  <p>lobortis nisl ut aliquip ex ea commodo consequat. Duis autem vel eum iriure dolor in hendrerit inilore eu feugiat nulla facilisis at vero..</p>
  <a class="btn-line" href="#">Read More</a>
</article>
<article class="post" style="left:622px">
  <div class="photo" role="img" aria-label="Photo of a wooden gavel resting on an open law book" style="background:linear-gradient(90deg,#e9eaee 0%,#c9a776 40%,#6b2a1e 70%,#d9d7d3 100%)">
    <div class="date"><b>08</b><span>JUNE</span></div>
  </div>
  <p>lobortis nisl ut aliquip ex ea commodo consequat. Duis autem vel eum iriure dolor in hendrerit in vulpue molestie ct, velo..</p>
  <a class="btn-line" href="#">Read More</a>
</article>

<footer class="footer">
  <div class="fwordmark">Aquilina Zerafa</div>
  <p class="copyright">Copyright © 2016 AZadvocates. All rights reserved.</p>

  <h4 class="fhead" style="left:465px">Navigation</h4>
  <div class="flinks">
    <a href="#" style="left:460px;top:92px">Home</a>
    <a href="#" style="left:588px;top:92px">About Malta</a>
    <a href="#" style="left:460px;top:131px">About us</a>
    <a href="#" style="left:588px;top:131px">Contact Us</a>
    <a href="#" style="left:460px;top:170px">Practice Areas</a>
  </div>
  <div class="fsocial"><i></i><i></i><i></i><i></i></div>

  <h4 class="fhead" style="left:799px">Newsletter</h4>
  <div class="newsletter">
    <div class="field">Enter Your Email</div>
    <div class="send"><svg width="18" height="16" viewBox="0 0 18 16" fill="none" stroke="#333" stroke-width="1.4"><path d="M1 7l16-6-4 14-5-5zM8 10l9-9"/></svg></div>
  </div>
  <div class="contact-line" style="left:807px;top:146px">
    <svg width="10" height="13" viewBox="0 0 10 13" fill="#ddd"><path d="M5 0a5 5 0 0 0-5 5c0 4 5 8 5 8s5-4 5-8a5 5 0 0 0-5-5zm0 7a2 2 0 1 1 0-4 2 2 0 0 1 0 4z"/></svg>
    <span>12 Harbour Lane, Senglea</span>
  </div>
  <div class="contact-line" style="left:807px;top:172px">
    <svg width="12" height="12" viewBox="0 0 12 12" fill="#ddd"><path d="M2 0l3 3-1.5 1.5c.8 1.6 2.2 3 3.8 3.8L9 7l3 3-2 2C5 12 0 7 0 2z"/></svg>
    <span>(356) 2000 4817</span>
  </div>
  <div class="contact-line" style="left:945px;top:172px">
    <svg width="14" height="10" viewBox="0 0 14 10" fill="#ddd"><path d="M0 0h14v10H0z"/><path d="M0 0l7 6 7-6" fill="none" stroke="#333" stroke-width="1.2"/></svg>
    <span>info@azadvocates.com</span>
  </div>
</footer>

</body>
</html>
```